Business Card Design

We need the business card for our new business based in St. Marys, we manufacture mainly bubble wraps. And we would like the design to use our company logo and also make it easy for people to understand right away we are bubble wrap manufacturer

Industry/Entity Type

Business

Contact Information for Business Card

Cushtane Pty Ltd, 14 Larkin Road Wrenford NSW 2774, Tel: 02 9471 5826, Fax: 9471 5839, Dara Oyelaran, General Manager, Mobile :0438 217 564, dara.oyelaran@cushtane.com.au, Website: cushtane.com.au

```html
<!DOCTYPE html>
<html lang="en">
<head>
<meta charset="utf-8">
<title>Cushtane Business Card</title>
<link rel="stylesheet" href="https://fonts.googleapis.com/css2?family=Arimo:wght@400;700&display=swap">
<style>
  :root {
    --backdrop: #e4e3e1;
    --card: #fbfbfb;
    --card-shade: #ececec;
    --brand-red: #c53538;
    --brand-grey: #6b6c6e;
    --bar-grey: #58595b;
    --ink: #1e1e1e;
    --ghost: #ededed;
  }
  html, body {
    margin: 0;
    padding: 0;
    overflow: hidden;
  }
  .canvas {
    position: relative;
    width: 1200px;
    height: 1023px;
    background: var(--backdrop);
    overflow: hidden;
    font-family: "Arimo", Arial, sans-serif;
  }
  .card {
    position: absolute;
    top: 200px;
    width: 380px;
    height: 620px;
    background: linear-gradient(160deg, var(--card) 0%, #ffffff 45%, var(--card-shade) 100%);
    box-shadow: 0 6px 18px rgba(0,0,0,0.18);
    overflow: hidden;
  }
  .card--front { left: 170px; }
  .card--back { left: 650px; }

  /* Wordmark */
  .wordmark {
    color: var(--brand-grey);
    font-weight: 700;
    letter-spacing: 1px;
    line-height: 1;
    white-space: nowrap;
  }
  .tagline {
    color: var(--brand-grey);
    font-size: 9px;
    letter-spacing: 4.2px;
    white-space: nowrap;
    text-transform: uppercase;
  }

  /* Front */
  .front-brand {
    position: absolute;
    top: 68px;
    left: 62px;
  }
  .front-brand .wordmark { font-size: 44px; }
  .front-brand .tagline { margin-top: 6px; font-size: 8px; letter-spacing: 3.6px; }

  .name-tab {
    position: absolute;
    left: 0;
    top: 178px;
    width: 14px;
    height: 42px;
    background: var(--brand-red);
  }
  .person {
    position: absolute;
    left: 36px;
    top: 176px;
    color: var(--ink);
  }
  .person__name { font-size: 27px; font-weight: 700; margin: 0; }
  .person__role { font-size: 14px; margin: 2px 0 0; }

  .contact-bar {
    position: absolute;
    left: 0;
    top: 282px;
    width: 14px;
    height: 150px;
    background: var(--bar-grey);
  }
  .contacts {
    position: absolute;
    left: 36px;
    top: 290px;
    margin: 0;
    padding: 0;
    list-style: none;
    color: var(--ink);
    font-size: 15px;
  }
  .contacts li {
    display: flex;
    align-items: center;
    height: 22px;
  }
  .contacts svg {
    width: 12px;
    height: 12px;
    margin-right: 10px;
    fill: var(--brand-red);
    flex: none;
  }
  .address {
    position: absolute;
    left: 36px;
    top: 420px;
    margin: 0;
    color: var(--ink);
    font-size: 13.5px;
    font-style: normal;
    line-height: 1.3;
  }
  .front-ghost {
    position: absolute;
    left: 180px;
    top: 420px;
    width: 300px;
    height: 60px;
    transform: rotate(-90deg);
    color: var(--ghost);
    font-size: 46px;
    font-weight: 700;
    line-height: 60px;
    text-align: center;
    white-space: nowrap;
  }

  /* Back */
  .back-band {
    position: absolute;
    left: 46px;
    width: 296px;
    height: 16px;
  }
  .back-band--top { top: 0; background: var(--brand-red); }
  .back-band--bottom { bottom: 0; background: var(--bar-grey); }
  .back-brand {
    position: absolute;
    left: 50%;
    top: 50%;
    transform: translate(-50%, -50%) rotate(90deg);
    text-align: left;
  }
  .back-brand .wordmark { font-size: 62px; }
  .back-brand .tagline { margin-top: 8px; font-size: 10px; letter-spacing: 5px; }
</style>
</head>
<body>
<main class="canvas">

  <section class="card card--front" aria-label="Card front">
    <div class="front-ghost" aria-hidden="true">CUSHTANE</div>

    <div class="front-brand">
      <div class="wordmark">CUSHTANE</div>
      <div class="tagline">Protective Packaging Solutions</div>
    </div>

    <div class="name-tab"></div>
    <div class="person">
      <p class="person__name">Dara Oyelaran</p>
      <p class="person__role">General Manager</p>
    </div>

    <div class="contact-bar"></div>
    <ul class="contacts">
      <li>
        <svg viewBox="0 0 12 12" aria-hidden="true"><path d="M2.5 0.5l2 2-1 1.6c.8 1.6 2 2.8 3.6 3.6l1.6-1 2 2-1.4 1.8C5 10.2 1.8 7 .7 1.9z"/></svg>
        02 9471 5826
      </li>
      <li>
        <svg viewBox="0 0 12 12" aria-hidden="true"><path d="M3 0h6v12H3zM4 1.5v8h4v-8zM5.4 10.2h1.2v1H5.4z" fill-rule="evenodd"/></svg>
        0438 217 564
      </li>
      <li>
        <svg viewBox="0 0 12 12" aria-hidden="true"><path d="M3 0h6v3H3zM0 4h12v5h-2v3H2V9H0zM3 7v4h6V7z" fill-rule="evenodd"/></svg>
        9471 5839
      </li>
      <li>
        <svg viewBox="0 0 12 12" aria-hidden="true"><path d="M6 0a6 6 0 1 0 0 12A6 6 0 0 0 6 0zm0 1.3c.8.8 1.3 2.4 1.4 4H4.6c.1-1.6.6-3.2 1.4-4zM4.6 6.7h2.8c-.1 1.6-.6 3.2-1.4 4-.8-.8-1.3-2.4-1.4-4zM1.4 5.3c.2-1.6 1.3-3 2.8-3.6-.6 1-.9 2.2-1 3.6zm0 1.4h1.8c.1 1.4.4 2.6 1 3.6-1.5-.6-2.600-2-2.8-3.6zm7.4 0h1.8c-.2 1.6-1.3 3-2.8 3.6.6-1 .9-2.2 1-3.6zm0-1.4c-.1-1.4-.4-2.6-1-3.6 1.5.6 2.6 2 2.8 3.6z"/></svg>
        www.cushtane.com.au
      </li>
      <li>
        <svg viewBox="0 0 12 12" aria-hidden="true"><path d="M0 2h12v8H0zM1.2 3.2v.4L6 6.6l4.8-3v-.4zM1.2 5v3.8h9.6V5L6 8z" fill-rule="evenodd"/></svg>
        dara.oyelaran@cushtane.com.au
      </li>
    </ul>

    <address class="address">
      Cushtane Pty Ltd, 14 Larkin Road<br>
      Wrenford NSW 2774
    </address>
  </section>

  <section class="card card--back" aria-label="Card back">
    <div class="back-band back-band--top"></div>
    <div class="back-brand">
      <div class="wordmark">CUSHTANE</div>
      <div class="tagline">Protective Packaging Solutions</div>
    </div>
    <div class="back-band back-band--bottom"></div>
  </section>

</main>
</body>
</html>
```